Oakmere Animal Care Group of Central Pennsylvania

I need a business card design for a new company in Harrisburg PA called "Animal Care Oakmere Group of Central PA". I will be providing relief services for veterinarians who need coverage during vacations; sick/maternity leave, etc. I would like to see the veterinarian symbol incorporated in the design in combination with animals (dogs /cats/birds/reptiles an pocket pets). Include My full name: Tomás R. Quintaval DVM, MLAS, BS. Also include my e mail (dvmtrq@mailbrook.net) and phone number 5552846017

Target Market(s)

Small Animal Veterinarian, practice owner

Industry/Entity Type

Business

Contact Information for Business Card

Oakmere Animal Care Group of Central PA

Font styles to use
Script

Requirements
Must have
• Veterinarian caduceus (see image) and Small animals (pets) within the logo.
Nice to have
• Give a sense of relaxation (vacationing)
Should not have
• Large animals, i.e. horses, cows, zoo animals...

```html
<!DOCTYPE html>
<html lang="en">
<head>
<meta charset="utf-8">
<title>Animal Care Oakmere Group of Central PA – Business Card</title>
<link href="https://fonts.googleapis.com/css2?family=Lobster+Two:ital,wght@1,700&family=Tinos:wght@400;700&display=swap" rel="stylesheet">
<style>
  :root {
    --page-bg: #d7dbdf;
    --card-white: #ffffff;
    --card-clear: #e8ebee;
    --navy: #0a5a94;
    --sky: #4ab8d4;
    --brand: #3fa6cc;
  }
  html, body {
    margin: 0;
    width: 1200px;
    height: 902px;
    overflow: hidden;
    background: var(--page-bg);
  }
  .card {
    position: absolute;
    left: 80px;
    top: 154px;
    width: 1040px;
    height: 594px;
    background: var(--card-clear);
    box-shadow: 0 6px 24px rgba(0, 0, 0, 0.15);
    overflow: hidden;
  }
  .card-shapes {
    position: absolute;
    inset: 0;
  }
  .holder-name {
    position: absolute;
    left: 53px;
    top: 160px;
    margin: 0;
    font-family: "Lobster Two", cursive;
    font-style: italic;
    font-weight: 700;
    font-size: 50px;
    line-height: 1;
    color: var(--sky);
  }
  .holder-title {
    position: absolute;
    left: 53px;
    top: 221px;
    margin: 0;
    font-family: "Tinos", serif;
    font-size: 29px;
    line-height: 1;
    color: var(--navy);
  }
  .contact-list {
    position: absolute;
    left: 53px;
    top: 398px;
    margin: 0;
    padding: 0;
    list-style: none;
    font-family: "Tinos", serif;
    font-size: 31px;
    color: var(--navy);
  }
  .contact-item {
    display: flex;
    align-items: center;
    gap: 22px;
    height: 38px;
  }
  .contact-icon {
    width: 27px;
    height: 27px;
    flex: none;
  }
  .brand {
    position: absolute;
    left: 620px;
    top: 140px;
    width: 360px;
    text-align: center;
  }
  .brand-mark {
    display: block;
    margin: 0 auto 20px;
  }
  .brand-name {
    margin: 0;
    font-family: "Tinos", serif;
    font-weight: 400;
    font-size: 27px;
    line-height: 1.25;
    color: var(--navy);
  }
  .brand-name span { display: block; }
</style>
</head>
<body>
  <section class="card">
    <svg class="card-shapes" width="1040" height="594" viewBox="0 0 1040 594">
      <polygon points="0,0 386,0 591,594 0,594" fill="var(--card-white)"/>
      <polygon points="386,0 451,0 606,594 591,594" fill="var(--navy)"/>
      <polygon points="451,0 457,0 611,594 606,594" fill="var(--card-white)"/>
    </svg>

    <h1 class="holder-name">Employee Name</h1>
    <p class="holder-title">Managing Director</p>

    <ul class="contact-list">
      <li class="contact-item">
        <svg class="contact-icon" viewBox="0 0 27 27" aria-hidden="true">
          <rect width="27" height="27" fill="var(--sky)"/>
          <path d="M6 10 Q13.5 5 21 10 L19 12 L16.5 11 L16 9.5 Q13.5 8.8 11 9.5 L10.5 11 L8 12 Z" fill="#fff"/>
          <rect x="8" y="13" width="11" height="8" rx="1.5" fill="#fff"/>
          <circle cx="13.5" cy="17" r="2" fill="var(--sky)"/>
        </svg>
        <span>5552846017</span>
      </li>
      <li class="contact-item">
        <svg class="contact-icon" viewBox="0 0 27 27" aria-hidden="true">
          <rect width="27" height="27" fill="var(--sky)"/>
          <rect x="5" y="7.5" width="17" height="12" fill="none" stroke="#fff" stroke-width="1.6"/>
          <path d="M5 7.5 L13.5 14.5 L22 7.5 M5 19.5 L11 13 M22 19.5 L16 13" fill="none" stroke="#fff" stroke-width="1.4"/>
        </svg>
        <span>dvmtrq@mailbrook.net</span>
      </li>
    </ul>

    <div class="brand">
      <svg class="brand-mark" width="140" height="140" viewBox="0 0 140 140" aria-hidden="true">
        <circle cx="70" cy="70" r="64" fill="none" stroke="var(--brand)" stroke-width="7"/>
      </svg>
      <p class="brand-name">
        <span>Animal Care</span>
        <span>Oakmere Group</span>
        <span>of Central PA</span>
      </p>
    </div>
  </section>
</body>
</html>
```